real estate managers brochure A5

Real estate services brochure (owners corporation management)

Content has been uploaded in MS word documents and we reserve the right to refine the text in one revision.

Visit out site http://www.marrowfen.com.au/body-corporate-managers/ and review the pages in the 'owners corporation' menu in our website - the brochure is for these services we provide.

We want to showcase a variety of 'trophy' buildings/unit/apartment/factory developments that we manage - I've uploaded these 'case studies' and high res images for each.

Some General services photos to be provided by you.

The brochure is given out to potential owners who we wish to be clients.

We are going to print a few dozen of these in hard copy so will need artwork in nigh resolution pdf format and a web resolution version for emailing potential clients.

Target Market(s)

Unit owners, apartment owners and commercial factory owners

Industry/Entity Type

Property Management

Font styles to use
Serif
Sans Serif

Requirements
Must have
• A modern design that looks like it could be just as home on a website or facebook post
• Have a flair of retro design and/or vintage graphics
• 3 full pages of example properties we manage property. see example properties in the case studies. I have uploaded high res images for the full page images and some brief text for these pages
Should not have
• Must not look like a typical real estate agents brochure (smiling agents, happy home owners)
• Images of people who do not look australian (ie afro american, asian) as this is not our target market. We typically have anglo australian or eruopean looking clients
• We are a young company who pride ourselves on. Efficient services and high tech management systems for the properties we manage

```html
<!DOCTYPE html>
<html lang="en">
<head>
<meta charset="utf-8">
<title>Marrowfen Owners Corporation Services</title>
<link href="https://fonts.googleapis.com/css2?family=Raleway:wght@400;700&display=swap" rel="stylesheet">
<style>
  :root {
    --sky: #1ba3df;
    --navy: #1f2b5c;
    --white: #ffffff;
    --ink: #1a1a1a;
  }
  * { margin: 0; padding: 0; box-sizing: border-box; }
  html, body { width: 845px; height: 1200px; overflow: hidden; background: var(--white); }
  .page {
    position: relative; width: 845px; height: 1200px; overflow: hidden;
    background: var(--sky); font-family: "Raleway", Arial, sans-serif;
  }
  .top-strip { position: absolute; left: 0; top: 0; width: 845px; height: 16px; background: var(--white); }
  .top-strip .rule { position: absolute; top: 5px; height: 5px; background: var(--navy); }
  .service { position: absolute; left: 28px; width: 790px; }
  .service h2 {
    position: relative; padding-left: 29px;
    color: var(--navy); font-weight: 700; font-size: 25px; line-height: 30px; letter-spacing: -0.2px;
  }
  .service h2::before {
    content: ""; position: absolute; left: 0; top: 9px; width: 13px; height: 13px; background: var(--white);
  }
  .service p {
    margin-top: 22px; padding-left: 29px;
    color: var(--white); font-size: 16.5px; line-height: 21px;
  }
  .payment-badge {
    position: absolute; left: 635px; top: 858px; width: 162px; height: 50px;
    background: var(--white); display: flex; align-items: center; justify-content: center; gap: 10px;
  }
  .payment-badge .mark { width: 26px; height: 26px; background: var(--ink); }
  .payment-badge .name { font-weight: 700; font-size: 30px; color: var(--ink); letter-spacing: 3px; }
  .office-photo {
    position: absolute; left: 0; top: 920px; width: 845px; height: 280px;
    background: linear-gradient(180deg, #5b87c9 0%, #8fb0dc 45%, #8a8f96 70%, #5f7f3f 88%, #3f6a2e 100%);
  }
</style>
</head>
<body>
<div class="page">
  <div class="top-strip">
    <span class="rule" style="left:0;width:380px"></span>
    <span class="rule" style="left:470px;width:375px;background:#3a6fb8"></span>
  </div>

  <section class="service" style="top:64px">
    <h2>Providing quality service since 2006</h2>
    <p>MARROWFEN is owned and operated by Coastline Habitat Property Pty Ltd, an Australian corporation trading since 2006. We are located at modern offices in Harbourvale.</p>
  </section>

  <section class="service" style="top:187px">
    <h2>Providing you with exceptional service</h2>
    <p>MARROWFEN offers a professional service with full quality control. We have experienced personnel, high tech systems, and well-organized procedures that we constantly improve.</p>
  </section>

  <section class="service" style="top:338px">
    <h2>Representatives of Australia’s leading owners corporation insurers</h2>
    <p>We deal directly with insurers so you have a single point of contact for claims and cut out the middle man brokers.</p>
  </section>

  <section class="service" style="top:464px">
    <h2>Experienced and qualified</h2>
    <p>Marrowfen Estate Agents are qualified, highly skilled professionals with combined real estate experience of 20+ years.</p>
  </section>

  <section class="service" style="top:589px">
    <h2>Adding value to owners corporation management</h2>
    <p>We’ll guide you by managing the affairs of your owners corporation, ensuring compliance and proactively assisting you to improve your property.</p>
  </section>

  <section class="service" style="top:712px">
    <h2>Easy to use payment systems</h2>
    <p>MARROWFEN offer a variety of ways to pay owners corporation contributions including BillDirect, Cheque, Cash, EFTlink and Credit Card using Eastgate Bank’s TALLY payment systems.</p>
  </section>

  <div class="payment-badge">
    <span class="mark"></span>
    <span class="name">TALLY</span>
  </div>

  <div class="office-photo" role="img" aria-label="Photo of the modern Marrowfen office and warehouse building under a blue sky with a green lawn in front"></div>
</div>
</body>
</html>
```